Stationery Design Project for Nimbora, Chicago

Nimbora, a street parking application which helps car drivers find a street parking spot by offering an ideal path along which to look for parking. This path is calculated by our algorithm based on data (e.g. historical data, baseball games schedule, etc.). Along this path the driver will find a spot and will also save 70% of the search time. Customer we target is reg. between 21 and 45 yo.

We envision something young, fresh, bright and original. Slightly abstract maybe. It should represent the idea and elements of finding street parking in the city, e.g. car(s), parking spot, people, city, etc. (just ideas!).

Logo is attached.

Requirement:
- Business Cards (2 Sided Full Color CMYK)
- Letterhead (1 Sided Full Color CMYK)
- Envelope (1 Sided Full Color CMYK)
- Sticker (1 Sided Full Color CMYK), round with a 2inch diameter.

Reason: We're starting to get more and more designs and need more time to look into all of them. Very exciting!! Thanks to everybody!

Hi all, we're in the process of selecting our favs. Though choices!!! Really good submissions. Will keep you posted and sorry for the delay.

Target Market(s)

Car drivers and owners between 21 and 45

Industry/Entity Type

Parking

Requirements
Must have
• Sticker should be round and include company URL nimbora.com and the new logo which we will attach soon.
Should not have
• Should not be too serious or boring.

```html
<!DOCTYPE html>
<html lang="en">
<head>
<meta charset="utf-8">
<title>Nimbora Business Card</title>
<link rel="stylesheet" href="https://fonts.googleapis.com/css2?family=Open+Sans:wght@400;600;700&display=swap">
<style>
  :root {
    --backdrop: #e4e5e7;
    --card-front: #ffffff;
    --card-back: #00aee6;
    --brand-ink: #1b1b1d;
    --mark-blue: #1f56b8;
    --text-grey: #555555;
    --rule-grey: #8a8a8a;
    --text-white: #ffffff;
  }
  * { margin: 0; padding: 0; box-sizing: border-box; }
  html, body { width: 954px; height: 1200px; overflow: hidden; }
  body {
    background: var(--backdrop);
    font-family: "Open Sans", Arial, sans-serif;
    position: relative;
  }
  .card {
    position: absolute;
    left: 78px;
    width: 797px;
    height: 455px;
    border-radius: 24px;
  }
  .card--front { top: 112px; background: var(--card-front); }
  .card--back { top: 672px; background: var(--card-back); }

  .brand {
    position: absolute;
    left: 122px;
    top: 68px;
    display: flex;
    align-items: center;
    gap: 28px;
  }
  .brand__dot {
    width: 156px;
    height: 156px;
    border-radius: 50%;
    background: var(--mark-blue);
  }
  .brand__name {
    position: relative;
    top: -10px;
    font-size: 90px;
    font-weight: 600;
    color: var(--brand-ink);
    letter-spacing: 1px;
    line-height: 1;
  }

  .contact {
    position: absolute;
    left: 0;
    right: 0;
    text-align: center;
    color: var(--text-grey);
    white-space: nowrap;
  }
  .contact--front { top: 276px; }
  .rule {
    display: block;
    height: 2px;
    margin: 0 auto;
    background: linear-gradient(90deg, transparent, var(--rule-grey), transparent);
  }
  .rule--top { width: 210px; margin-bottom: 6px; }
  .rule--bottom { width: 290px; margin-top: 2px; margin-bottom: 3px; }
  .contact__name { font-size: 24px; font-weight: 700; line-height: 32px; }
  .contact__role { font-size: 19px; }
  .contact__line { font-size: 21.5px; line-height: 37px; }
  .contact__label { font-weight: 700; }
  .gap { display: inline-block; width: 14px; }

  .contact--back {
    top: 382px;
    color: var(--text-white);
  }
</style>
</head>
<body>
  <section class="card card--front">
    <div class="brand">
      <span class="brand__dot"></span>
      <span class="brand__name">Nimbora</span>
    </div>
    <div class="contact contact--front">
      <span class="rule rule--top"></span>
      <p class="contact__name">Your Name - <span class="contact__role">Designation</span></p>
      <span class="rule rule--bottom"></span>
      <p class="contact__line"><span class="contact__label">t</span> : 123-456-7890<span class="gap"></span><span class="contact__label">c</span> : 123-456-7890</p>
      <p class="contact__line"><span class="contact__label">e</span> : name@nimbora.com<span class="gap"></span><span class="contact__label">w</span> : www.nimbora.com</p>
      <p class="contact__line">City Name, Street Name, State Name, Country Code</p>
    </div>
  </section>

  <section class="card card--back">
    <div class="brand">
      <span class="brand__dot"></span>
      <span class="brand__name">Nimbora</span>
    </div>
    <div class="contact contact--back">
      <p class="contact__line"><span class="contact__label">e</span> : name@nimbora.com<span class="gap"></span><span class="contact__label">w</span> : www.nimbora.com</p>
    </div>
  </section>
</body>
</html>
```